Business card design for Automotive workshop

We need a business card for a new automotive repair and tyre shop called Keelstone Prime Automotive located in New Zealand. We are a clean, modern and fresh workshop and company.

Front needs to feature logo,
my name:
Marlo Fenwicke (director)

Address:
48 Tarn Lane
Whitianga 3510

Phone: 07 594 2713
Mobile: 027 451 9362
Email: office@keelstoneautomotive.example.nz
Website: keelstoneautomotive.example.nz

Back needs to feature an area to write down appointment details, date and time.

Also feature a list of jobs and work we do such as,
Vehicle Servicing
All Mechanical Repairs
Warrant of Fitness
Tyres & Wheel Alignments
Automotive Diagnostics
Automotive Parts & Supplies

```html
<!DOCTYPE html>
<html lang="en">
<head>
<meta charset="utf-8">
<title>Keelstone Prime Automotive – Business Card</title>
<link href="https://fonts.googleapis.com/css2?family=Lato:wght@400;700;900&display=swap" rel="stylesheet">
<style>
  :root {
    --red: #e31b23;
    --charcoal: #3a3a3c;
    --ink: #2b2b2b;
    --muted: #555;
    --paper: #ffffff;
    --stage: #1c1c1c;
    --line: #444;
    --band-dark: #1a1a1a;
  }
  * { box-sizing: border-box; margin: 0; padding: 0; }
  html, body { width: 1200px; height: 852px; overflow: hidden; }
  body {
    background: var(--stage);
    font-family: "Lato", Arial, sans-serif;
    display: flex; flex-direction: column; align-items: center; justify-content: center;
    gap: 40px;
  }
  .card {
    position: relative; width: 630px; height: 360px;
    background: var(--paper); overflow: hidden;
    box-shadow: 0 10px 30px rgba(0,0,0,.6);
  }

  /* Back */
  .card-back__top {
    position: absolute; inset: 0 0 auto 0; height: 220px;
    background: var(--charcoal);
    border-bottom: 5px solid var(--red);
    display: flex; flex-direction: column; align-items: center; justify-content: center;
    gap: 22px;
  }
  .wordmark {
    display: flex; align-items: center; gap: 10px;
    font-weight: 900; letter-spacing: .5px; color: var(--red); white-space: nowrap;
  }
  .wordmark__square { width: 16px; height: 16px; background: var(--red); flex: none; }
  .card-back .wordmark { font-size: 30px; }
  .services {
    list-style: none; color: #fff; font-size: 15px; line-height: 1.5;
    display: grid; grid-template-columns: auto auto;
  }
  .services li { padding: 0 10px; }
  .services li:nth-child(odd) { text-align: right; border-right: 1.5px solid var(--red); }
  .appointment {
    position: absolute; left: 0; right: 0; top: 225px; bottom: 0;
    padding: 22px 48px 0;
  }
  .appointment__title { text-align: center; color: var(--red); font-size: 16px; margin-bottom: 28px; }
  .appointment__fields { display: flex; gap: 16px; color: var(--muted); font-size: 15px; }
  .field { flex: 1; display: flex; align-items: flex-end; gap: 6px; }
  .field__line { flex: 1; border-bottom: 1px solid var(--line); height: 1px; }

  /* Front */
  .card-front .wordmark { position: absolute; left: 34px; top: 150px; font-size: 20px; gap: 8px; }
  .card-front .wordmark__square { width: 13px; height: 13px; }
  .person { position: absolute; right: 40px; top: 40px; text-align: right; }
  .person__name { color: var(--red); font-size: 30px; font-weight: 700; line-height: 1.15; }
  .person__role { color: var(--muted); font-size: 15px; }
  .person__rule { position: absolute; right: 40px; top: 112px; width: 280px; border-top: 1px solid var(--red); }
  .address { position: absolute; right: 40px; top: 126px; text-align: right; color: var(--muted); font-size: 15px; line-height: 1.35; }
  .contacts-rule { position: absolute; left: 34px; top: 240px; width: 220px; border-top: 1px solid var(--red); }
  .contacts { position: absolute; left: 34px; top: 252px; list-style: none; color: var(--ink); font-size: 15px; line-height: 1.45; }
  .contacts li { display: flex; align-items: center; gap: 8px; }
  .contacts svg { width: 11px; height: 11px; fill: none; stroke: var(--red); stroke-width: 2; flex: none; }
  .corner-band { position: absolute; right: 0; bottom: 0; width: 300px; height: 170px; }
  .corner-band__red { fill: var(--red); }
  .corner-band__dark { fill: var(--band-dark); }
</style>
</head>
<body>
  <section class="card card-back" aria-label="Card back">
    <div class="card-back__top">
      <div class="wordmark"><span class="wordmark__square"></span>KEELSTONE PRIME AUTOMOTIVE</div>
      <ul class="services">
        <li>Vehicle Servicing</li><li>All Mechanical Repairs</li>
        <li>Warrant of Fitness</li><li>Tyres &amp; Wheel Alignments</li>
        <li>Automotive Diagnostics</li><li>Automotive Parts &amp; Supplies</li>
      </ul>
    </div>
    <div class="appointment">
      <p class="appointment__title">Appointment</p>
      <div class="appointment__fields">
        <div class="field">Date <span class="field__line"></span></div>
        <div class="field">Time <span class="field__line"></span></div>
      </div>
    </div>
  </section>

  <section class="card card-front" aria-label="Card front">
    <div class="person">
      <p class="person__name">Marlo Fenwicke</p>
      <p class="person__role">Director</p>
    </div>
    <div class="person__rule"></div>
    <p class="address">48 Tarn Lane<br>Whitianga 3510</p>
    <div class="wordmark"><span class="wordmark__square"></span>KEELSTONE PRIME AUTOMOTIVE</div>
    <div class="contacts-rule"></div>
    <ul class="contacts">
      <li><svg viewBox="0 0 12 12"><path d="M2 1l3 0 1 3-2 1a6 6 0 0 0 3 3l1-2 3 1v3c-6 0-9-3-9-9z"/></svg>07 594 2713</li>
      <li><svg viewBox="0 0 12 12"><rect x="3" y="1" width="6" height="10" rx="1"/></svg>027 451 9362</li>
      <li><svg viewBox="0 0 12 12"><rect x="1" y="3" width="10" height="7"/><path d="M1 3l5 4 5-4"/></svg>office@keelstoneautomotive.example.nz</li>
      <li><svg viewBox="0 0 12 12"><circle cx="6" cy="6" r="5"/><path d="M1 6h10M6 1c-3 3-3 7 0 10M6 1c3 3 3 7 0 10"/></svg>keelstoneautomotive.example.nz</li>
    </ul>
    <svg class="corner-band" viewBox="0 0 300 170" preserveAspectRatio="none" aria-hidden="true">
      <polygon class="corner-band__red" points="300,0 300,170 40,170 55,115 110,115 110,105"/>
      <polygon class="corner-band__dark" points="0,170 40,170 55,115 40,130"/>
    </svg>
  </section>
</body>
</html>
```